Carpet cleaning company focused on high quality needs business cards

We are a growing company that just merged with another company and need to design a new business card. We do both residential as well as commercial cleaning. We do carpet, tile & grout, upholstery, hard floors, and stain & pet odor removal. We treat our customers like family and strive to achieve outstanding results with every job.

```html
<!DOCTYPE html>
<html lang="en">
<head>
<meta charset="utf-8">
<title>Harborline Floorcare – Business Card</title>
<link rel="stylesheet" href="https://fonts.googleapis.com/css2?family=Montserrat:wght@500;600&display=swap">
<style>
  :root {
    --backdrop: #2b2b2e;
    --card: #ffffff;
    --ink: #1a1a1a;
    --accent: #e8423a;
    --muted: #2e2e2e;
  }
  * { box-sizing: border-box; margin: 0; padding: 0; }
  html, body { width: 1200px; height: 900px; overflow: hidden; }
  body {
    background: var(--backdrop);
    font-family: "Montserrat", sans-serif;
    color: var(--ink);
    display: flex;
    flex-direction: column;
    align-items: center;
    justify-content: center;
    gap: 36px;
  }
  .card {
    width: 700px;
    height: 400px;
    background: var(--card);
    border-radius: 28px;
    position: relative;
    overflow: hidden;
  }
  .brand {
    display: flex;
    align-items: center;
    white-space: nowrap;
  }
  .brand-dot {
    background: var(--accent);
    border-radius: 50%;
    flex: none;
  }
  .brand-name {
    font-weight: 600;
    color: var(--ink);
    line-height: 1;
  }

  .card-front .brand {
    position: absolute;
    left: 50%;
    top: 50%;
    transform: translate(-50%, -50%);
    gap: 16px;
  }
  .card-front .brand-dot { width: 26px; height: 26px; }
  .card-front .brand-name { font-size: 40px; }

  .card-back .brand {
    position: absolute;
    left: 56px;
    top: 50%;
    transform: translateY(-50%);
    gap: 10px;
  }
  .card-back .brand-dot { width: 14px; height: 14px; }
  .card-back .brand-name { font-size: 21px; }

  .divider {
    position: absolute;
    left: 372px;
    top: 90px;
    width: 2px;
    height: 220px;
    background: var(--accent);
  }
  .contact {
    position: absolute;
    left: 400px;
    top: 78px;
    width: 280px;
  }
  .person-name {
    font-size: 27px;
    font-weight: 600;
    color: var(--accent);
    line-height: 1.1;
  }
  .person-role {
    font-size: 14px;
    font-weight: 500;
    color: var(--muted);
    margin-top: 2px;
  }
  .address {
    font-size: 13px;
    font-weight: 500;
    color: var(--muted);
    margin-top: 14px;
    line-height: 1.4;
  }
  .contact-list {
    list-style: none;
    margin-top: 16px;
  }
  .contact-list li {
    display: flex;
    align-items: center;
    gap: 10px;
    font-size: 13px;
    font-weight: 500;
    color: var(--muted);
    line-height: 1.85;
  }
  .contact-list svg {
    width: 13px;
    height: 13px;
    flex: none;
    fill: var(--accent);
  }
</style>
</head>
<body>

  <section class="card card-front" aria-label="Card front">
    <div class="brand">
      <span class="brand-dot"></span>
      <span class="brand-name">Harborline Floorcare</span>
    </div>
  </section>

  <section class="card card-back" aria-label="Card back">
    <div class="brand">
      <span class="brand-dot"></span>
      <span class="brand-name">Harborline Floorcare</span>
    </div>

    <span class="divider"></span>

    <div class="contact">
      <h1 class="person-name">Daniel Reyes</h1>
      <p class="person-role">CEO</p>
      <p class="address">418 Maple Grove Ave, #114<br>Lakeford, OH 43190</p>
      <ul class="contact-list">
        <li>
          <svg viewBox="0 0 16 16" aria-hidden="true"><path d="M3.6 1.2l2.3 2.6-1.2 1.8c.9 2 2.6 3.7 4.6 4.6l1.8-1.2 2.6 2.3-1.1 2.3C7.5 13.8 2.2 8.5 1.3 3.4z"/></svg>
          555 210-4876
        </li>
        <li>
          <svg viewBox="0 0 16 16" aria-hidden="true"><path d="M4.5 0.5h7a1 1 0 0 1 1 1v13a1 1 0 0 1-1 1h-7a1 1 0 0 1-1-1v-13a1 1 0 0 1 1-1zm.6 2v9.5h5.8V2.5zM8 12.8a.9.9 0 1 0 0 1.8.9.9 0 0 0 0-1.8z"/></svg>
          555 210-4876
        </li>
        <li>
          <svg viewBox="0 0 16 16" aria-hidden="true"><path d="M1 3h14v10H1zm1.6 1.4L8 8.6l5.4-4.2z"/></svg>
          info@harborlinefloors.com
        </li>
        <li>
          <svg viewBox="0 0 16 16" aria-hidden="true"><path d="M8 1a7 7 0 1 0 0 14A7 7 0 0 0 8 1zm0 1.6c.8 1 1.4 2.6 1.5 4.6h-3c.1-2 .7-3.6 1.5-4.6zM2.7 8.8h2.4c.1 1.6.5 3 1.1 4.1A5.4 5.4 0 0 1 2.7 8.8zm0-1.6a5.4 5.4 0 0 1 3.5-4.1c-.6 1.1-1 2.5-1.1 4.1zm5.3 6.2c-.8-1-1.4-2.6-1.5-4.6h3c-.1 2-.7 3.6-1.5 4.6zm1.8-.5c.6-1.1 1-2.5 1.1-4.1h2.4a5.4 5.4 0 0 1-3.5 4.1zm1.1-5.7c-.1-1.6-.5-3-1.1-4.1a5.4 5.4 0 0 1 3.5 4.1z"/></svg>
          www.harborlinefloors.com
        </li>
      </ul>
    </div>
  </section>

</body>
</html>
```